Los Brava Dip – CPG Website with WordPress - Store Locator: WP Maps plugin

Larkfield Food Company is a startup consumer packaged goods (CPG) brand launching its flagship product line — Los Brava Dip. We’re seeking a talented web designer to create a bold, professional, mobile-optimized website using WordPress with a WP Maps store locator to help customers find local retailers.

Our goal is to build a strong online presence that supports both retail growth and direct-to-consumer sales.

See Los Brava _Website_Design_Brief word document.

The website URL is https://losbravadip.example/

Target Market(s)

Consumers of gourmet salsa

Industry/Entity Type

Consumer Packaged Goods - Salsa manufacturer.

Coding

Coded - Design and coding required

Number of Pages Required

5+ page

Requirements
Must have
• The design of the Los Brava Dip website shall emulate the clean, polished aesthetic of Fennigo.example.

```html
<!DOCTYPE html>
<html lang="en">
<head>
<meta charset="utf-8">
<title>Our Recipes – Los Brava</title>
<link href="https://fonts.googleapis.com/css2?family=Josefin+Sans:wght@400;600;700&family=Roboto+Condensed:wght@700&display=swap" rel="stylesheet">
<style>
:root{
  --red:#c8202b;
  --green:#2e6b1f;
  --ink:#111111;
  --muted:#555555;
  --border:#b9b9b9;
  --white:#ffffff;
  --black:#000000;
  --orange:#e8711a;
}
*{box-sizing:border-box;margin:0;padding:0}
html,body{width:1200px;height:2749px;overflow:hidden}
body{position:relative;background:var(--white);font-family:"Josefin Sans",sans-serif;color:var(--ink)}

.site-header{position:absolute;top:0;left:0;width:1200px;height:79px;background:var(--white);z-index:3}
.brand-tab{position:absolute;left:98px;top:-40px;width:162px;height:144px;border-radius:50%;background:var(--white)}
.brand-name{position:absolute;left:112px;top:24px;width:135px;text-align:center;font-size:30px;font-weight:700;color:var(--red);line-height:1}
.main-nav{position:absolute;top:34px;left:324px;display:flex;gap:0}
.main-nav a{font-size:14px;font-weight:600;letter-spacing:1.3px;color:var(--ink);text-decoration:none;text-transform:uppercase}
.nav-about{position:absolute;left:0}
.nav-products{position:absolute;left:105px;white-space:nowrap}
.nav-where{position:absolute;left:241px;white-space:nowrap}
.nav-recipes{position:absolute;left:410px;padding-bottom:6px;border-bottom:2px solid var(--red)}
.nav-review{position:absolute;left:525px}
.btn-contact{position:absolute;left:934px;top:23px;width:130px;height:35px;border-radius:18px;background:var(--red);color:var(--white);font-size:14px;font-weight:600;letter-spacing:1.3px;display:flex;align-items:center;justify-content:center;padding-top:3px}

.hero{position:absolute;top:79px;left:0;width:1200px;height:325px;overflow:hidden}
.hero-art{position:absolute;inset:0;background:linear-gradient(100deg,#f4a62a 0%,#ec8418 30%,#d9561a 55%,#a8261a 75%,#6a1810 100%)}
.hero-title{position:absolute;left:0;width:1200px;top:114px;text-align:center;font-family:"Roboto Condensed",sans-serif;font-size:62px;font-weight:700;color:var(--white);letter-spacing:1px}
.hero-underline{position:absolute;left:498px;top:182px}

.recipe-grid{position:absolute;top:483px;left:89px;width:1009px}
.recipe-card{position:absolute;width:326px;height:406px;border:1px solid var(--border);background:var(--white)}
.recipe-photo{height:231px;width:100%}
.recipe-body{padding:18px 26px 0 26px}
.recipe-title{font-size:19.5px;font-weight:600;line-height:1.2;color:var(--ink);margin-bottom:9px;height:48px}
.recipe-text{font-size:12.5px;line-height:1.4;color:var(--muted);height:38px;overflow:hidden}
.btn-read{display:inline-flex;align-items:center;gap:6px;margin-top:12px;width:127px;height:34px;justify-content:center;background:var(--green);color:var(--white);font-size:12px;font-weight:600;letter-spacing:1.2px;padding-top:3px}
.btn-read svg{margin-top:-3px}

.follow{position:absolute;top:2262px;left:0;width:1200px;height:280px;overflow:hidden}
.follow-art{position:absolute;inset:0;background:linear-gradient(100deg,#de4e22 0%,#d84120 40%,#c22a1f 70%,#9b1b1b 100%)}
.follow-rule{position:absolute;left:385px;width:406px;height:1px;background:rgba(255,255,255,.8)}
.follow-title{position:absolute;top:64px;left:0;width:1200px;text-align:center;color:var(--white);font-size:30px;font-weight:700;letter-spacing:1.5px}
.social-ring{position:absolute;top:142px;width:80px;height:80px;border:2px solid var(--white);border-radius:50%;display:flex;align-items:center;justify-content:center;color:var(--white);font-size:12px;font-weight:600;text-align:center}

.site-footer{position:absolute;top:2542px;left:0;width:1200px;height:207px;background:var(--black);color:var(--white)}
.footer-brand{position:absolute;left:70px;top:85px;width:190px;text-align:center;font-size:34px;font-weight:700;color:var(--red)}
.footer-divider-v{position:absolute;left:300px;top:0;width:1px;height:207px;background:#333}
.footer-divider-h{position:absolute;left:301px;top:115px;width:899px;height:1px;background:#333}
.footer-nav{position:absolute;top:73px;left:354px;display:flex;align-items:center;font-size:14px;font-weight:600;letter-spacing:1.3px}
.footer-nav a{color:var(--white);text-decoration:none}
.footer-nav .dot{width:5px;height:5px;background:var(--red);margin:0 26px 3px}
.copyright{position:absolute;top:145px;left:349px;font-size:13px}
.footer-social{position:absolute;top:136px;left:795px;display:flex;gap:6px}
.footer-social span{width:28px;height:28px;border-radius:50%;border:2px solid var(--white)}
.legal{position:absolute;top:145px;left:883px;font-size:13px;display:flex;gap:14px}
</style>
</head>
<body>

<header class="site-header">
  <div class="brand-tab"></div>
  <div class="brand-name">Los Brava</div>
  <nav class="main-nav">
    <a class="nav-about" href="#">About</a>
    <a class="nav-products" href="#">Products</a>
    <a class="nav-where" href="#">Where to Buy</a>
    <a class="nav-recipes" href="#">Recipes</a>
    <a class="nav-review" href="#">Review</a>
  </nav>
  <a class="btn-contact" href="#">CONTACT&nbsp;<svg width="7" height="10" viewBox="0 0 7 10"><path d="M1 1l4 4-4 4" stroke="#fff" stroke-width="1.6" fill="none"/></svg></a>
</header>

<section class="hero">
  <div class="hero-art" role="img" aria-label="Warm orange and red flame-shaped background artwork"></div>
  <h1 class="hero-title">OUR RECIPES</h1>
  <svg class="hero-underline" width="262" height="12" viewBox="0 0 262 12"><path d="M2 9 C80 3 180 2 260 6" stroke="#fff" stroke-width="4" fill="none" stroke-linecap="round"/></svg>
</section>

<main class="recipe-grid">
  <article class="recipe-card" style="left:0;top:0">
    <div class="recipe-photo" role="img" aria-label="Baked chicken with melted cheese and rice on a blue plate" style="background:linear-gradient(135deg,#d9a24a,#c48a3c 50%,#1f3a7a)"></div>
    <div class="recipe-body">
      <h2 class="recipe-title">Baked Chicken with Salsa and Sour Cream</h2>
      <p class="recipe-text">Looking for a quick, hearty dish that doesn't skimp on flavor?</p>
      <a class="btn-read">READ MORE <svg width="6" height="9" viewBox="0 0 6 9"><path d="M1 1l3.5 3.5L1 8" stroke="#fff" stroke-width="1.5" fill="none"/></svg></a>
    </div>
  </article>
  <article class="recipe-card" style="left:341px;top:0">
    <div class="recipe-photo" role="img" aria-label="Spoonful of cheesy Mexican beef and rice" style="background:linear-gradient(135deg,#e2b58a,#c9662a 50%,#a5481c)"></div>
    <div class="recipe-body">
      <h2 class="recipe-title">One Pot Mexican<br>Beef and Rice</h2>
      <p class="recipe-text">This One Pot Mexican Beef and Rice is the ultimate weeknight dinner—quick to prepare</p>
      <a class="btn-read">READ MORE <svg width="6" height="9" viewBox="0 0 6 9"><path d="M1 1l3.5 3.5L1 8" stroke="#fff" stroke-width="1.5" fill="none"/></svg></a>
    </div>
  </article>
  <article class="recipe-card" style="left:683px;top:2px">
    <div class="recipe-photo" role="img" aria-label="Bowls of black bean soup topped with fresh salsa" style="background:linear-gradient(135deg,#6e3f4a,#7c4a55 55%,#2aa8b8 80%,#4e8a2a)"></div>
    <div class="recipe-body">
      <h2 class="recipe-title">Los Brava's Black Bean<br>and Salsa Soup</h2>
      <p class="recipe-text">Looking for a quick, hearty dish that doesn't skimp on flavor? Our Black Bean and Salsa</p>
      <a class="btn-read">READ MORE <svg width="6" height="9" viewBox="0 0 6 9"><path d="M1 1l3.5 3.5L1 8" stroke="#fff" stroke-width="1.5" fill="none"/></svg></a>
    </div>
  </article>

  <article class="recipe-card" style="left:0;top:435px">
    <div class="recipe-photo" role="img" aria-label="Oven-baked salsa chicken with melted cheddar" style="background:linear-gradient(135deg,#e8a63a,#b8432a 55%,#7a2a1a)"></div>
    <div class="recipe-body">
      <h2 class="recipe-title">Los Brava's Zesty Oven-Baked Salsa Chicken</h2>
      <p class="recipe-text">When you're short on time but still want a flavorful, satisfying meal, this Zesty</p>
      <a class="btn-read">READ MORE <svg width="6" height="9" viewBox="0 0 6 9"><path d="M1 1l3.5 3.5L1 8" stroke="#fff" stroke-width="1.5" fill="none"/></svg></a>
    </div>
  </article>
  <article class="recipe-card" style="left:341px;top:435px">
    <div class="recipe-photo" role="img" aria-label="Rice bowl with salsa beef, avocado and greens" style="background:linear-gradient(135deg,#6a9a3a,#c5b86a 45%,#b84a2a 75%,#eeeeee)"></div>
    <div class="recipe-body">
      <h2 class="recipe-title">Slow Cooker Salsa Beef</h2>
      <p class="recipe-text" style="height:54px">This Slow Cooker Salsa Beef is a weeknight lifesaver that's equal parts hearty, flavorful, and hands-off. Just a handful of ingredients</p>
      <a class="btn-read" style="margin-top:-4px">READ MORE <svg width="6" height="9" viewBox="0 0 6 9"><path d="M1 1l3.5 3.5L1 8" stroke="#fff" stroke-width="1.5" fill="none"/></svg></a>
    </div>
  </article>
  <article class="recipe-card" style="left:683px;top:437px">
    <div class="recipe-photo" role="img" aria-label="Skillet of pork in green chile salsa" style="background:linear-gradient(135deg,#d9d3c6,#6f7028 45%,#3a3a2a 80%)"></div>
    <div class="recipe-body">
      <h2 class="recipe-title">Los Brava's Green Chile<br>Pork Skillet</h2>
      <p class="recipe-text">Bring bold, zesty flavor to your table with this savory Pork in Salsa Verde.</p>
      <a class="btn-read">READ MORE <svg width="6" height="9" viewBox="0 0 6 9"><path d="M1 1l3.5 3.5L1 8" stroke="#fff" stroke-width="1.5" fill="none"/></svg></a>
    </div>
  </article>

  <article class="recipe-card" style="left:0;top:871px">
    <div class="recipe-photo" role="img" aria-label="Shredded chicken taco with cilantro and avocado" style="background:linear-gradient(135deg,#c86a3a,#e6c48a 50%,#8aa04a)"></div>
    <div class="recipe-body">
      <h2 class="recipe-title">Bold &amp; Saucy Shredded Chicken</h2>
      <p class="recipe-text">If you're looking for a set-it-and-forget-it meal that delivers big on flavor</p>
      <a class="btn-read">READ MORE <svg width="6" height="9" viewBox="0 0 6 9"><path d="M1 1l3.5 3.5L1 8" stroke="#fff" stroke-width="1.5" fill="none"/></svg></a>
    </div>
  </article>
  <article class="recipe-card" style="left:341px;top:871px">
    <div class="recipe-photo" role="img" aria-label="Chicken burger with lime wedges and salsa" style="background:linear-gradient(135deg,#b8a88a,#8ab04a 40%,#c88a4a 70%,#e9e0d0)"></div>
    <div class="recipe-body">
      <h2 class="recipe-title">Spiced-Up Chicken<br>Burgers with a Kick</h2>
      <p class="recipe-text">This One Pot Mexican Beef and Rice is the ultimate weeknight dinner—quick to prepare</p>
      <a class="btn-read">READ MORE <svg width="6" height="9" viewBox="0 0 6 9"><path d="M1 1l3.5 3.5L1 8" stroke="#fff" stroke-width="1.5" fill="none"/></svg></a>
    </div>
  </article>
  <article class="recipe-card" style="left:683px;top:873px">
    <div class="recipe-photo" role="img" aria-label="Tex-Mex skillet with rice, chips, cheese and sour cream on a blue plate" style="background:linear-gradient(135deg,#2a56b0,#d8c8a0 45%,#c8823a 75%,#2a4aa0)"></div>
    <div class="recipe-body">
      <h2 class="recipe-title">Los Brava's Tex-Mex Skillet<br>Fiesta</h2>
      <p class="recipe-text">This hearty and flavorful skillet dish brings together everything you love about</p>
      <a class="btn-read">READ MORE <svg width="6" height="9" viewBox="0 0 6 9"><path d="M1 1l3.5 3.5L1 8" stroke="#fff" stroke-width="1.5" fill="none"/></svg></a>
    </div>
  </article>

  <article class="recipe-card" style="left:3px;top:1299px">
    <div class="recipe-photo" role="img" aria-label="Cheesy salsa chicken topped with green onions" style="background:linear-gradient(135deg,#e8a63a,#b8432a 55%,#8a7a6a)"></div>
    <div class="recipe-body">
      <h2 class="recipe-title" style="height:24px">Cheesy Salsa Chicken</h2>
      <p class="recipe-text" style="height:54px">This Cheesy Salsa Chicken is a go-to dinner recipe that delivers bold flavor with minimal effort. Perfect for busy weeknights, it fea-</p>
      <a class="btn-read">READ MORE <svg width="6" height="9" viewBox="0 0 6 9"><path d="M1 1l3.5 3.5L1 8" stroke="#fff" stroke-width="1.5" fill="none"/></svg></a>
    </div>
  </article>
</main>

<section class="follow">
  <div class="follow-art" role="img" aria-label="Red and orange flame-shaped background artwork"></div>
  <div class="follow-rule" style="top:55px"></div>
  <h2 class="follow-title">FOLLOW US ON</h2>
  <div class="follow-rule" style="top:104px"></div>
  <a class="social-ring" style="left:493px">Friend<br>wall</a>
  <a class="social-ring" style="left:597px">Snap<br>grid</a>
</section>

<footer class="site-footer">
  <div class="footer-brand">Los Brava</div>
  <div class="footer-divider-v"></div>
  <nav class="footer-nav">
    <a href="#">ABOUT</a><span class="dot"></span>
    <a href="#">PRODUCTS</a><span class="dot"></span>
    <a href="#">WHERE TO BUY</a><span class="dot"></span>
    <a href="#">RECIPES</a><span class="dot"></span>
    <a href="#">REVIEW</a><span class="dot"></span>
    <a href="#">CONTACT</a>
  </nav>
  <div class="footer-divider-h"></div>
  <p class="copyright">© 2025 Los Brava All rights reserved.</p>
  <div class="footer-social" aria-label="Friendwall and Snapgrid"><span></span><span></span></div>
  <div class="legal"><span>Privacy Policy</span><span>Terms of Use</span></div>
</footer>

</body>
</html>
```